Flat bootstrap design for existing site

I'm looking for a modern flat design based around an existing logo. This has to be a custom design (no external templates), and implemented into a bootstrap framework.

The logo is attached as 2 versions - choose whichever you want, that flows better with whatever design you choose.

Added screenshots of the existing site (currently using the default bootstrap layouts). Please make your designs around those pages in the screenshots (i.e. the homepage only has the postal code input and the header). The active page has 3 screenshots, because I wanted to illustrate the other states that would be visible (in the table rows).

This is a moving/junk removal website, just for some context.

Here's some example websites (flat designs) that I like, just to give you an idea of what I'm after.

https://www.plimvora.com/
https://dacklow.com/
https://trevanu.com/
https://quobrintal.com/en/

Coding

Coded - Design and coding required

Number of Pages Required

5+ page

Colors

Designer to choose colors to be used in the design.

Requirements
Must have
• It must be a modern/simple flat design, that is built around the existing logo (attached).
• It has to be implemented using bootstrap.

```html
<!DOCTYPE html>
<html lang="en">
<head>
<meta charset="utf-8">
<title>Booking Details</title>
<link href="https://fonts.googleapis.com/css2?family=Figtree:wght@300;400;500;600;700&display=swap" rel="stylesheet">
<style>
:root{
  --brand:#45c3ef;
  --bg:#e9e9eb;
  --white:#ffffff;
  --ink:#1d1d1f;
  --muted:#6b6b6b;
  --line:#c9c9cc;
  --head:#f2f2f2;
  --green:#6ab04c;
  --orange:#f15a22;
}
*{box-sizing:border-box;margin:0;padding:0}
html,body{width:1200px;height:1022px;overflow:hidden}
body{background:var(--bg);font-family:"Figtree",sans-serif;color:var(--ink);position:relative}
.abs{position:absolute}
.site-header{position:absolute;left:0;top:0;width:1200px;height:85px;background:var(--white)}
.brand{left:130px;top:24px;display:flex;align-items:center;gap:8px;color:var(--brand);font-weight:700;font-size:26px;letter-spacing:1px}
.brand-dot{width:16px;height:16px;border-radius:50%;background:var(--brand)}
.nav-link{top:33px;font-size:11.5px;letter-spacing:.3px}
.nav-cta{left:797px;top:26px;width:125px;height:29px;border:1px solid var(--brand);color:var(--brand);font-size:11.5px;display:flex;align-items:center;justify-content:center;letter-spacing:.3px}
.account{left:942px;top:33px;font-size:11px;display:flex;align-items:center;gap:8px}
.card{position:absolute;left:132px;width:937px;background:var(--white)}
.card-title{position:absolute;left:29px;color:var(--brand);font-size:22px;font-weight:600;letter-spacing:.4px}
.field-label{position:absolute;font-size:11.5px;letter-spacing:.2px}
.field{position:absolute;border:1px solid var(--line);font-size:11px;color:var(--muted);font-weight:300;letter-spacing:.4px;padding:0 16px;display:flex;align-items:center;justify-content:space-between}
.field.textarea{align-items:flex-start;padding-top:14px}
.btn-update{position:absolute;left:386px;top:352px;width:164px;height:45px;background:var(--brand);color:var(--white);font-size:19px;font-weight:700;letter-spacing:1px;display:flex;align-items:center;justify-content:center}
.lead{position:absolute;left:30px;top:55px;font-size:14px}
.drivers{position:absolute;left:31px;top:102px;width:877px;height:254px;border:1px solid var(--line)}
.drivers-head{position:absolute;left:0;top:0;width:100%;height:45px;background:var(--head);border-bottom:1px solid var(--line)}
.col-h{position:absolute;top:15px;font-size:11.5px;font-weight:700}
.cell{position:absolute;font-size:12.5px}
.dash{position:absolute;width:14px;height:1px;background:var(--ink)}
.row-rule{position:absolute;left:18px;width:829px;height:1px;background:#dcdcde}
.status{position:absolute;left:603px;width:122px;height:26px;color:var(--white);font-size:11.5px;font-weight:600;display:flex;align-items:center;justify-content:center;letter-spacing:.2px}
.status.accepted{background:var(--green)}
.status.sent{background:var(--brand)}
.status.pending{background:var(--orange)}
.payment{position:absolute;left:752px;font-size:11.5px;font-weight:600;color:var(--muted);letter-spacing:.2px}
</style>
</head>
<body>
<header class="site-header">
  <div class="abs brand"><span class="brand-dot"></span>HAULNEST</div>
  <div class="abs nav-link" style="left:628px">BOOK</div>
  <div class="abs nav-link" style="left:689px">HOW IT WORKS</div>
  <div class="nav-cta abs">BECOME A DRIVER</div>
  <div class="account abs">maria@plunvet.com
    <svg width="11" height="7" viewBox="0 0 11 7"><path d="M1 1l4.5 4.5L10 1" fill="none" stroke="#555" stroke-width="1.3"/></svg>
  </div>
</header>

<section class="card" style="top:118px;height:430px">
  <h1 class="card-title" style="top:22px">BOOKING DETAILS</h1>
  <div class="field-label" style="left:42px;top:86px">PACKAGE SELECTED</div>
  <div class="field-label" style="left:475px;top:86px">PICK UP TIME SELECTED</div>
  <div class="field" style="left:43px;top:112px;width:389px;height:46px">PACKAGE 1
    <svg width="11" height="7" viewBox="0 0 11 7"><path d="M1 1l4.5 4.5L10 1" fill="none" stroke="#555" stroke-width="1.3"/></svg>
  </div>
  <div class="field" style="left:476px;top:112px;width:389px;height:46px">JULY 17 AT 8.30 PM
    <svg width="16" height="16" viewBox="0 0 16 16" fill="none" stroke="#777" stroke-width="1"><rect x="1" y="2.5" width="14" height="12.5"/><path d="M1 6h14M4.5 1v3M11.5 1v3M1 9h14M1 12h14M4.5 6v9M8 6v9M11.5 6v9"/></svg>
  </div>
  <div class="field-label" style="left:42px;top:179px">DESCRIPTION</div>
  <div class="field textarea" style="left:43px;top:205px;width:822px;height:119px">1 LARGE STOVE</div>
  <div class="btn-update">UPDATE</div>
</section>

<section class="card" style="top:586px;height:391px">
  <h2 class="card-title" style="top:22px">DRIVERS IN YOUR AREA</h2>
  <p class="lead">Please stay on this page and be patient, while we contact the drivers and find you one ASAP</p>
  <div class="drivers">
    <div class="drivers-head">
      <div class="col-h" style="left:31px">NAME</div>
      <div class="col-h" style="left:236px">DISTANCE (KM)</div>
      <div class="col-h" style="left:416px">AGREED PICKUP TIME</div>
    </div>

    <div class="cell" style="left:32px;top:74px">Dorian Malick</div>
    <div class="cell" style="left:236px;top:74px">4.04km Away</div>
    <div class="cell" style="left:423px;top:74px">July 18 at 4:14 pm</div>
    <div class="status accepted" style="top:62px">TIME ACCEPTED</div>
    <div class="payment" style="top:68px">PAYMENT MADE</div>
    <div class="row-rule" style="top:102px"></div>

    <div class="cell" style="left:32px;top:120px">Tobin Greer</div>
    <div class="cell" style="left:236px;top:120px">5.7km Away</div>
    <div class="dash" style="left:423px;top:133px"></div>
    <div class="status sent" style="top:116px">REQUEST SENT</div>
    <div class="row-rule" style="top:149px"></div>

    <div class="cell" style="left:32px;top:166px">Elric Vanner</div>
    <div class="cell" style="left:236px;top:166px">11.13km Away</div>
    <div class="dash" style="left:423px;top:179px"></div>
    <div class="status sent" style="top:162px">REQUEST SENT</div>
    <div class="row-rule" style="top:200px"></div>

    <div class="cell" style="left:32px;top:213px">Wade Corlan</div>
    <div class="cell" style="left:236px;top:213px">11.91km Away</div>
    <div class="dash" style="left:423px;top:226px"></div>
    <div class="status pending" style="top:215px">PENDING</div>
  </div>
</section>
</body>
</html>
```